Business card design for Brivo Engineering Tandem

We need a new business card design along with all the necessary to place an order. The company is Brivo Engineering Tandem and we recently updated our logo.

```html
<!DOCTYPE html>
<html lang="en">
<head>
<meta charset="UTF-8">
<title>Brivo Engineering Tandem – Business Card</title>
<link href="https://fonts.googleapis.com/css2?family=Montserrat:wght@400;700&display=swap" rel="stylesheet">
<style>
  :root {
    --backdrop: #d3d8d8;
    --card-white: #f1f0ee;
    --brand-yellow: #d8b512;
    --accent-yellow: #e6c21c;
    --ink: #2e2e2e;
    --ink-soft: #4a4a4a;
    --logo-tone: #b99a08;
  }
  * { margin: 0; padding: 0; box-sizing: border-box; }
  html, body {
    width: 1200px;
    height: 881px;
    overflow: hidden;
    background: var(--backdrop);
    font-family: "Montserrat", sans-serif;
  }
  .sheet {
    position: relative;
    width: 1200px;
    height: 881px;
    display: flex;
    align-items: center;
    justify-content: center;
    gap: 60px;
  }
  .card {
    width: 500px;
    height: 286px;
    position: relative;
  }
  .card-front {
    background: var(--card-white);
    border-bottom: 3px solid var(--accent-yellow);
  }
  .identity {
    position: absolute;
    right: 258px;
    top: 108px;
    text-align: right;
  }
  .person-name {
    color: var(--accent-yellow);
    font-weight: 700;
    font-size: 19px;
    letter-spacing: 0.5px;
    line-height: 1.2;
  }
  .person-role {
    color: var(--ink-soft);
    font-size: 12px;
    margin-top: 3px;
  }
  .divider {
    position: absolute;
    left: 256px;
    top: 104px;
    width: 2px;
    height: 62px;
    background: var(--accent-yellow);
  }
  .contacts {
    position: absolute;
    left: 272px;
    top: 106px;
    list-style: none;
  }
  .contacts li {
    display: flex;
    align-items: center;
    gap: 7px;
    color: var(--ink);
    font-size: 12px;
    line-height: 20px;
  }
  .contacts svg { width: 10px; height: 10px; fill: var(--accent-yellow); flex: none; }
  .card-back {
    background: var(--brand-yellow);
    display: flex;
    align-items: center;
    justify-content: center;
    gap: 14px;
  }
  .brand-mark {
    width: 22px;
    height: 22px;
    background: var(--logo-tone);
    flex: none;
  }
  .brand-name {
    color: var(--logo-tone);
    font-weight: 700;
    font-size: 20px;
    letter-spacing: 1.5px;
    text-transform: uppercase;
  }
</style>
</head>
<body>
<main class="sheet">
  <section class="card card-front">
    <div class="identity">
      <p class="person-name">DANIEL REYES</p>
      <p class="person-role">Managing Director</p>
    </div>
    <div class="divider"></div>
    <ul class="contacts">
      <li>
        <svg viewBox="0 0 10 10" aria-hidden="true"><path d="M2 0.5 L3.8 0.5 L4.3 3 L3.2 3.9 Q4.3 6 6.1 6.8 L7 5.7 L9.5 6.2 L9.5 8 Q9.5 9.5 8 9.5 Q0.5 9 0.5 2 Q0.5 0.5 2 0.5 Z"/></svg>
        555 010 2040
      </li>
      <li>
        <svg viewBox="0 0 10 10" aria-hidden="true"><path d="M0.5 2 H9.5 V8.5 H0.5 Z M0.5 2 L5 5.5 L9.5 2" stroke="#f1f0ee" stroke-width="0.8"/></svg>
        info@brivotandem.net
      </li>
      <li>
        <svg viewBox="0 0 10 10" aria-hidden="true"><circle cx="5" cy="5" r="4.5"/><path d="M0.5 5 H9.5 M5 0.5 V9.5" stroke="#f1f0ee" stroke-width="0.7"/></svg>
        www.brivotandem.net
      </li>
    </ul>
  </section>

  <section class="card card-back">
    <span class="brand-mark" aria-hidden="true"></span>
    <span class="brand-name">Brivo Engineering Tandem</span>
  </section>
</main>
</body>
</html>
```